Business Card Design

Want something very unique. No business, just personal. The image I submitted is for inspiration only.

Target Market(s)

friends and new acquaintances

Industry/Entity Type

Business

Contact Information for Business Card

Dora Malcott
Santa Fe, NM
505-718-2946
doramalcott@quellmail.net

```html
<!DOCTYPE html>
<html lang="en">
<head>
<meta charset="utf-8">
<title>Dora Malcott – Personal Card</title>
<link rel="stylesheet" href="https://fonts.googleapis.com/css2?family=Fira+Sans:wght@400;700&display=swap">
<style>
  :root {
    --backdrop: #7a2428;
    --card: #f4f4f4;
    --card-light: #fbfbfb;
    --ink: #141414;
    --halftone: #6e6e6e;
    --photo-earth: #8a5a3a;
    --photo-sand: #c9b48e;
    --photo-sky: #d8d6c8;
  }
  html, body {
    margin: 0;
    padding: 0;
    width: 1200px;
    height: 853px;
    overflow: hidden;
    background: var(--backdrop);
  }
  .canvas {
    position: relative;
    width: 1200px;
    height: 853px;
    display: flex;
    align-items: center;
    justify-content: center;
  }
  .card {
    position: relative;
    width: 420px;
    height: 760px;
    background: var(--card);
    overflow: hidden;
    box-shadow: 0 10px 30px rgba(0,0,0,0.35);
  }
  .card__chevron {
    position: absolute;
    top: 0;
    left: 0;
    width: 420px;
    height: 150px;
  }
  .card__photo {
    position: absolute;
    top: 130px;
    left: 0;
    width: 420px;
    height: 300px;
    background: linear-gradient(160deg, var(--photo-sky) 0%, var(--photo-sand) 40%, var(--photo-earth) 100%);
  }
  .card__halo {
    position: absolute;
    top: 380px;
    left: 50%;
    width: 320px;
    height: 320px;
    margin-left: -160px;
    border-radius: 50%;
    background: var(--card-light);
  }
  .card__details {
    position: absolute;
    top: 458px;
    left: 0;
    width: 100%;
    text-align: center;
    font-family: "Fira Sans", sans-serif;
    color: var(--ink);
  }
  .card__name {
    margin: 0;
    font-weight: 700;
    font-size: 27px;
    line-height: 1.25;
  }
  .card__phone {
    margin: 16px 0 0;
    font-weight: 400;
    font-size: 31px;
  }
  .card__email {
    margin: 12px 0 0;
    font-weight: 400;
    font-size: 26px;
  }
  .card__halftone-band {
    position: absolute;
    left: 0;
    bottom: 0;
    width: 420px;
    height: 78px;
    background: linear-gradient(180deg, rgba(110,110,110,0.45) 0%, var(--halftone) 100%);
  }
</style>
</head>
<body>
  <main class="canvas">
    <article class="card">
      <svg class="card__chevron" viewBox="0 0 420 150" role="img" aria-label="Halftone dot chevron pattern">
        <polygon points="0,0 70,0 210,95 350,0 420,0 420,20 210,150 0,20" fill="var(--halftone)"/>
      </svg>
      <div class="card__photo" role="img" aria-label="Photograph of two people crouching beside resting cheetahs in a fenced enclosure"></div>
      <div class="card__halo"></div>
      <div class="card__details">
        <p class="card__name">Dora Malcott Santa Fe,<br>NM</p>
        <p class="card__phone">505-718-2946</p>
        <p class="card__email">doramalcott@quellmail.net</p>
      </div>
      <div class="card__halftone-band" role="img" aria-label="Halftone dot band"></div>
    </article>
  </main>
</body>
</html>
```